Velura Nocturna

Website for a night club with live music and cabaret dancers. I would like to have the following Menu: 1.) Home; 2) The Facilities; 3) The Show; 4) Other Attractions; 5) Videos & Fotos; 6) Program; 7) Reservations; 8) Membership; 9) Contacts.

The pages should be easily editable and allow to enter text, including the menu since the final version will be in both English and Portuguese. It should have a toggle or links for the Portuguese language and the English Language.

The night club itself is called "VELURA NOCTURNA"; and its URL is www.veluranocturna.example.

```html
<!DOCTYPE html>
<html lang="en">
<head>
<meta charset="utf-8">
<title>Velura Nocturna</title>
<link href="https://fonts.googleapis.com/css2?family=Mulish:wght@400;600;700&family=Open+Sans:wght@400;600&display=swap" rel="stylesheet">
<style>
:root{
  --black:#000;
  --green-top:#0c1602;
  --green:#6a9e08;
  --green-bright:#8cc63f;
  --leaf:#7fb52a;
  --gold:#f0b51e;
  --gold-dark:#c98a0c;
  --yellow:#f4c20d;
  --text:#e8e8e8;
  --panel:#1b1b1b;
  --footer:#1a1a1a;
  --btn:#3d7a0a;
}
*{margin:0;padding:0;box-sizing:border-box}
html,body{width:904px;height:1200px;overflow:hidden}
body{position:relative;background:var(--black);font-family:"Open Sans",sans-serif;color:var(--text)}
a{text-decoration:none}
.abs{position:absolute}
.header-band{left:0;top:0;width:904px;height:353px;background:linear-gradient(180deg,var(--green-top) 0%,#2f5004 30%,var(--green) 100%)}
.brand{left:114px;top:18px;display:flex;align-items:center;gap:10px}
.brand-dot{width:50px;height:50px;border-radius:50%;background:var(--gold)}
.brand-name{font-family:"Mulish",sans-serif;font-weight:700;font-size:26px;color:var(--leaf);line-height:1}
.top-links{right:110px;top:8px;font-family:"Mulish",sans-serif;font-size:12px;color:#fff;white-space:nowrap}
.top-links a{color:#fff}
.top-links span{margin:0 6px}
.lang{left:710px;top:50px;width:82px;height:24px;background:#333a2d;border:1px solid #4d5546;display:flex;align-items:center;justify-content:center;gap:6px;font-size:9.5px;color:#fff}
.flag{width:15px;height:10px;background:linear-gradient(135deg,#223e8c 40%,#c8102e 40% 60%,#223e8c 60%)}
.caret{width:0;height:0;border-left:4px solid transparent;border-right:4px solid transparent;border-top:5px solid #fff}
.main-nav{left:110px;top:84px;width:685px;height:40px;background:linear-gradient(180deg,var(--gold) 0%,var(--gold-dark) 100%);font-family:"Mulish",sans-serif;font-size:13.5px;font-weight:400}
.main-nav a{position:absolute;top:11px;color:#fff;white-space:nowrap;line-height:18px}
.slider{left:110px;top:124px;width:684px;height:314px;background:linear-gradient(135deg,#4a3a2a 0%,#b8b22a 30%,#d9c83a 50%,#5a8f4a 70%,#2a2a24 100%);border-bottom:2px solid var(--gold)}
.slide-caption{left:133px;top:231px;width:277px;height:121px;background:rgba(20,20,20,.78);padding:16px 28px}
.slide-caption h2{font-family:"Mulish",sans-serif;font-weight:600;font-size:24px;line-height:29px;color:#fff;white-space:nowrap}
.slide-caption p{font-size:8.5px;line-height:14px;color:#ddd;margin-top:6px}
.dots{left:431px;top:418px;display:flex;gap:3px}
.dots i{width:9px;height:9px;border-radius:50%;background:#fff;display:block}
.arrow{top:211px}
.welcome{left:118px;top:470px;width:660px}
.welcome h1{font-family:"Mulish",sans-serif;font-weight:400;font-size:24px;color:#fff;white-space:nowrap}
.welcome .lead{font-size:11px;color:#ddd;margin-top:6px;padding-left:2px}
.welcome .body{font-size:8.8px;line-height:15px;color:#ccc;margin-top:9px;padding-left:2px}
.card{top:600px;width:161px}
.card .photo{height:89px}
.card h3{font-family:"Mulish",sans-serif;font-weight:600;font-size:14.5px;color:var(--green-bright);margin-top:12px;margin-left:-2px}
.card p{font-size:8.6px;line-height:13.5px;color:#ccc;margin-top:3px;margin-left:-2px}
.btn{display:inline-block;margin-top:10px;margin-left:-2px;width:70px;height:20px;background:var(--btn);border:1px solid #5a9a1a;color:#fff;font-size:8.5px;line-height:18px;text-align:center}
.divider{left:104px;top:829px;width:688px;height:1px;background:#333}
.section-title{font-family:"Mulish",sans-serif;font-weight:400;font-size:21px}
.latest-title{left:112px;top:858px;color:#fff}
.show{display:flex;gap:9px;width:220px}
.show .thumb{width:99px;height:69px;flex:none}
.show h4{font-family:"Mulish",sans-serif;font-weight:600;font-size:12.5px;color:var(--yellow)}
.show p{font-size:8.6px;line-height:13.5px;color:#ccc;margin-top:3px}
.contact-title{left:597px;top:856px;color:var(--gold)}
.contact-box{left:599px;top:891px;width:193px;height:183px;background:var(--panel);border:1px solid #333}
.contact-photo{height:99px;background:linear-gradient(180deg,#8a9298 0%,#4c5a52 55%,#2a3a22 100%)}
.contact-info{padding:5px 17px}
.contact-info .label{color:var(--leaf);font-size:10.5px}
.contact-info .addr{font-size:7.8px;color:#ddd;margin-top:4px;white-space:nowrap}
.contact-info .phone{font-size:14px;color:#fff;margin-top:2px}
.contact-info .mail{font-size:8.5px;color:#ddd;margin-top:2px}
.site-footer{left:0;top:1124px;width:904px;height:76px;background:var(--footer)}
.foot-nav{left:117px;top:1145px;display:flex;gap:27px;font-family:"Mulish",sans-serif;font-size:12px;color:#ddd}
.foot-nav a{color:#ddd}
.copy{left:117px;top:1166px;font-size:8.5px;color:#aaa}
.social{left:719px;top:1149px;display:flex;gap:3px}
.social i{display:block;width:19px;height:19px;border-radius:50%;background:#fff}
</style>
</head>
<body>
<div class="abs header-band"></div>

<header>
  <div class="abs brand"><div class="brand-dot"></div><div class="brand-name">Velura Nocturna</div></div>
  <nav class="abs top-links"><a href="#">Home</a><span>|</span><a href="#">Membership</a><span>|</span><a href="#">Contacts</a></nav>
  <div class="abs lang"><div class="flag" role="img" aria-label="English language flag"></div>English<div class="caret"></div></div>
  <nav class="abs main-nav">
    <a href="#" style="left:24px">The Facilities</a>
    <a href="#" style="left:135px">The Show</a>
    <a href="#" style="left:227px">Other Attractions</a>
    <a href="#" style="left:366px">Videos &amp; Fotos</a>
    <a href="#" style="left:488px">Reservations</a>
    <a href="#" style="left:598px">Program</a>
  </nav>
</header>

<section>
  <div class="abs slider" role="img" aria-label="Cabaret dancers in colourful feathered costumes"></div>
  <svg class="abs arrow" style="left:42px" width="26" height="54" viewBox="0 0 26 54"><polyline points="24,1 2,27 24,53" fill="none" stroke="#fff" stroke-width="1.3"/></svg>
  <svg class="abs arrow" style="left:829px" width="26" height="54" viewBox="0 0 26 54"><polyline points="2,1 24,27 2,53" fill="none" stroke="#fff" stroke-width="1.3"/></svg>
  <div class="abs slide-caption">
    <h2>NIGHT CLUB<br>WITH LIVE MUSIC</h2>
    <p>Vivamus porttitor purus nisl eleifend libero a tempus libero lectus feugiat felis Morbi diam mauris</p>
  </div>
  <div class="abs dots"><i></i><i></i><i></i><i></i></div>
</section>

<section class="abs welcome">
  <h1>Welcome to Velura Nocturna Mainpage</h1>
  <p class="lead">Mauris vel lacus vitae felis vestibulum volutpat Etiam est nunc venenatis in tristique eu imperdiet</p>
  <p class="body">Cum sociis natoque penatibus et magnis dis parturient montes nascetur ridiculus mus In iaculis facilisis massa Etiam eu urna Sed porta Suspendisse quam leo molestie sed luctus quis feugiat in pede Fusce tellus Sed metus augue convallis et vehicula ut pulvinar eu ante Integer orci</p>
</section>

<section>
  <div class="abs card" style="left:114px">
    <div class="photo" role="img" aria-label="Dancer on a red-curtained stage" style="background:linear-gradient(180deg,#b01818,#7a0e0e)"></div>
    <h3>The Facilities</h3>
    <p>Mauris vel lacus vitae felis vestibulum volutpat Etiam est nunc venenatis in tristique eu imperdiet ac nis</p>
    <a class="btn" href="#">CLICK HERE</a>
  </div>
  <div class="abs card" style="left:287px">
    <div class="photo" role="img" aria-label="Dancers with drums on stage" style="background:linear-gradient(135deg,#8a2a1a,#c9b04a 50%,#4a6a8a)"></div>
    <h3>Video &amp; Fotos</h3>
    <p>Mauris vel lacus vitae felis vestibulum volutpat Etiam est nunc venenatis in tristique eu imperdiet ac nis</p>
    <a class="btn" href="#">CLICK HERE</a>
  </div>
  <div class="abs card" style="left:460px">
    <div class="photo" role="img" aria-label="Performers in red feathered headdresses" style="background:linear-gradient(135deg,#c81a2a,#e8c8b0 60%,#d04040)"></div>
    <h3>Reservation</h3>
    <p>Mauris vel lacus vitae felis vestibulum volutpat Etiam est nunc venenatis in tristique eu imperdiet ac nis</p>
    <a class="btn" href="#">CLICK HERE</a>
  </div>
  <div class="abs card" style="left:632px">
    <div class="photo" role="img" aria-label="Performers in white feathered headdresses" style="background:linear-gradient(135deg,#e8e8ec,#d8b8a8 55%,#b8b8c0)"></div>
    <h3>Membership</h3>
    <p>Mauris vel lacus vitae felis vestibulum volutpat Etiam est nunc venenatis in tristique eu imperdiet ac nis</p>
    <a class="btn" href="#">CLICK HERE</a>
  </div>
</section>

<div class="abs divider"></div>

<section>
  <h2 class="abs section-title latest-title">Latest Shows</h2>
  <div class="abs show" style="left:112px;top:901px">
    <div class="thumb" role="img" aria-label="Couples dancing at a party" style="background:linear-gradient(135deg,#3a2a6a,#c83a4a 60%,#1a1a2a)"></div>
    <div><h4>Show Tittle here</h4><p>Mauris vel lacus vitae felis vestibulum volutpat Etiam est nunc venenatis in tris-tique eu impe</p></div>
  </div>
  <div class="abs show" style="left:345px;top:902px">
    <div class="thumb" role="img" aria-label="Dancers under club lights" style="background:linear-gradient(135deg,#2a3a8a,#c84a9a 55%,#2a1a3a)"></div>
    <div><h4>Show Tittle here</h4><p>Mauris vel lacus vitae felis vestibulum volutpat Etiam est nunc venenatis in tris-tique eu impe</p></div>
  </div>
  <div class="abs show" style="left:112px;top:997px">
    <div class="thumb" role="img" aria-label="Concert crowd with raised hands" style="background:linear-gradient(180deg,#c8c8e8,#7a5aa8 50%,#3a2a5a)"></div>
    <div><h4>Show Tittle here</h4><p>Mauris vel lacus vitae felis vestibulum volutpat Etiam est nunc venenatis in tris-tique eu impe</p></div>
  </div>
  <div class="abs show" style="left:345px;top:998px">
    <div class="thumb" role="img" aria-label="Friends toasting with drinks" style="background:linear-gradient(135deg,#2a1a1a,#b87a4a 50%,#3a2020)"></div>
    <div><h4>Show Tittle here</h4><p>Mauris vel lacus vitae felis vestibulum volutpat Etiam est nunc venenatis in tris-tique eu impe</p></div>
  </div>
</section>

<aside>
  <h2 class="abs section-title contact-title">Contact Us</h2>
  <div class="abs contact-box">
    <div class="contact-photo" role="img" aria-label="Club building with palm trees"></div>
    <div class="contact-info">
      <div class="label">Address:</div>
      <div class="addr">48 Marlow Ave #3B Lisbon 1200-021 PT</div>
      <div class="phone">555.014.7730</div>
      <div class="mail">info@veluranocturna.example</div>
    </div>
  </div>
</aside>

<footer>
  <div class="abs site-footer"></div>
  <nav class="abs foot-nav"><a href="#">Home</a><a href="#">About Us</a><a href="#">Services</a><a href="#">Products</a><a href="#">Video</a><a href="#">Contact</a></nav>
  <div class="abs copy">© 2014 Company Name&nbsp; All right reserved &nbsp;|&nbsp; Term of Use</div>
  <div class="abs social" aria-label="Social links"><i></i><i></i><i></i></div>
</footer>
</body>
</html>
```